Hvac and insulation company needs good looking business card design

We are hvac and insulation company and looking for a new business cards that look to today standards designs

Target Market(s)

homeowners

Industry/Entity Type

Hvac

Contact Information for Business Card

Name: Walter Brinoku
Home comfort consultant
address: 4827 Dunmore St #215 Oakland, CA 94619
office: 888-316-2790
cell: 510-742-3185
Lic.# 584261
Email: walter@corvane-hvac.com
Web: corvane-hvac.com

Requirements
Must have
• clean and sleek look
Nice to have
• simple with a clean look
Should not have
• to busy business card

```html
<!DOCTYPE html>
<html lang="en">
<head>
<meta charset="utf-8">
<title>Corvane business card</title>
<link rel="stylesheet" href="https://fonts.googleapis.com/css2?family=Arimo:wght@400;500;700&display=swap">
<style>
  :root {
    --backdrop: #2f2f2f;
    --card-white: #ffffff;
    --brand-orange: #f28522;
    --band-grey: #7d7d7d;
    --ink: #1f1f1f;
  }
  * { margin: 0; padding: 0; box-sizing: border-box; }
  html, body { width: 1200px; height: 900px; overflow: hidden; }
  body {
    background: var(--backdrop);
    font-family: "Arimo", Arial, sans-serif;
    position: relative;
  }
  .card {
    position: absolute;
    top: 306px;
    width: 439px;
    height: 271px;
    box-shadow: 2px 3px 6px rgba(0,0,0,0.55);
    overflow: hidden;
  }
  .card--front { left: 149px; background: var(--card-white); }
  .card--back { left: 608px; background: var(--brand-orange); }

  .corner-tabs { position: absolute; left: 0; top: 26px; }
  .holder-name {
    position: absolute; left: 39px; top: 29px;
    font-size: 20px; font-weight: 700; color: var(--brand-orange);
  }
  .holder-title {
    position: absolute; left: 39px; top: 52px;
    font-size: 12.5px; color: var(--ink);
  }

  .wordmark {
    position: absolute;
    display: flex; align-items: center; gap: 14px;
    font-weight: 500; letter-spacing: 0.5px; line-height: 1;
  }
  .wordmark__mark { display: block; border-radius: 6px; }
  .card--front .wordmark { right: 26px; top: 98px; font-size: 44px; color: var(--brand-orange); }
  .card--front .wordmark__mark { width: 44px; height: 44px; background: var(--brand-orange); }
  .card--back .wordmark { left: 50%; transform: translateX(-50%); top: 110px; font-size: 44px; color: var(--card-white); }
  .card--back .wordmark__mark { width: 44px; height: 44px; background: var(--card-white); }

  .contact-list {
    position: absolute; left: 28px; top: 179px;
    list-style: none; font-size: 12.5px; color: var(--ink);
  }
  .contact-list li { display: flex; align-items: center; height: 16px; }
  .contact-list svg { width: 11px; height: 11px; margin-right: 3px; flex: none; }

  .office-details {
    position: absolute; right: 24px; top: 188px;
    text-align: right; font-size: 12.5px; color: var(--ink); line-height: 16px;
  }
  .office-details .licence { margin-bottom: 7px; }
  .office-details .licence-label { color: var(--brand-orange); }

  .footer-bands { position: absolute; left: 0; bottom: 0; }

  .back-url {
    position: absolute; left: 0; right: 0; top: 229px;
    text-align: center; font-size: 12.5px; color: var(--card-white);
  }
</style>
</head>
<body>
  <section class="card card--front" aria-label="Card front">
    <svg class="corner-tabs" width="30" height="38" viewBox="0 0 30 38">
      <polygon points="0,0 12,0 16,37 0,37" fill="var(--band-grey)"/>
      <polygon points="11,0 28,0 28,37 15,37" fill="var(--brand-orange)"/>
    </svg>
    <div class="holder-name">Walter Brinoku</div>
    <div class="holder-title">Home Comfort Consultant</div>

    <div class="wordmark"><span class="wordmark__mark"></span>corvane</div>

    <ul class="contact-list">
      <li>
        <svg viewBox="0 0 12 12"><path d="M1 4.5C1 3 3 2 6 2s5 1 5 2.5v1H8.5V4.3H3.5v1.2H1z M2.5 6.5h7L10.5 10h-9z" fill="var(--brand-orange)"/></svg>
        888-316-2790
      </li>
      <li>
        <svg viewBox="0 0 12 12"><rect x="3" y="0.8" width="6" height="10.4" rx="1.2" fill="none" stroke="var(--brand-orange)" stroke-width="1.3"/><circle cx="6" cy="9.3" r="0.6" fill="var(--brand-orange)"/></svg>
        510-742-3185
      </li>
      <li>
        <svg viewBox="0 0 12 12"><rect x="0.5" y="2.5" width="11" height="7.5" fill="var(--brand-orange)"/><path d="M0.8 3l5.2 4 5.2-4" fill="none" stroke="#fff" stroke-width="0.9"/></svg>
        walter@corvane-hvac.com
      </li>
      <li>
        <svg viewBox="0 0 12 12"><circle cx="6" cy="6" r="5" fill="var(--brand-orange)"/><path d="M3 4.5c1.5-.5 2 .8 1.3 1.8-.6.9.4 2 .2 3M7.5 2.5c-.3 1 .8 1.3 1.8 1.2M8 7.5c.8-.2 1.5.3 1.7 1" fill="none" stroke="#fff" stroke-width="0.8"/></svg>
        www.corvane-hvac.com
      </li>
    </ul>

    <div class="office-details">
      <p class="licence"><span class="licence-label">LIC.</span># 584261</p>
      <p>4827 Dunmore St</p>
      <p>#215 Oakland, CA 94619</p>
    </div>

    <svg class="footer-bands" width="439" height="20" viewBox="0 0 439 20">
      <rect x="0" y="6" width="218" height="14" fill="var(--band-grey)"/>
      <polygon points="206,20 227,2 439,2 439,20" fill="#fff"/>
      <polygon points="209,20 226,3 439,3 439,20" fill="var(--brand-orange)"/>
    </svg>
  </section>

  <section class="card card--back" aria-label="Card back">
    <div class="wordmark"><span class="wordmark__mark"></span>corvane</div>
    <div class="back-url">www.corvane-hvac.com</div>
  </section>
</body>
</html>
```